A unique communication angle to crowdfunding

Looking for a fresh redesign of a crowd funding website that deals in real estate. I already have the content, but am looking to take the design to the next level.

Existing real estate crowd funding sites focus on the real estate. I want to explore communication angle that:
- puts the investor in the centre of the communication: "become a baron"
- highlights the international nature (international properties, international investors)

There's also quite a lot of copy on the site, as we need to explain the service in quite a bit of detail. There's room to reduce the copy and replace with graphics. Could also consider clicking to see different text (see our difference section in http://galleonfairs.com)

The backend of the platform is already being worked on by a specialist crowd funding service provider.

In total there are 5 pages to be designed.

The homepage is really important. Right now it looks quite dated. It doesn't have a great layout. Note there is no mobile version of the website, so the pages need to be seen well on mobile devices. When looking at the brief, refer to the following links too:

current website:
http://pennyduke.com

some revisions made so far:
http://preview.stakeharbor.com/7K3LQ9

Attached are logo files and another file which contained copy for the pages. No need to rework the logo.

Please make sure to use the same copy in the brief on the webpages, to ensure the layouts work. Designers are free to propose images they feel work on the pages.

I would like to see if rather than tweaking the pages, it's possible to come up with a better design concept. If the 5 pages are accepted, there's a chance I'll request an additional 4 pages.
Updates

Please note the font used in the logo is called "harabara" in case you decide to use it in any of the titles, etc.

Please note there is one additional page for which we would like to review designs. Note the page would be a template to be used on all future real estate detail pages. Here is an example of the current design for reference:

http://pennyduke.com/projects/view/14

In total there are 5 page designs required, (homepage + 4)

Thank you

FYI -

Just a quick note to give information from similar UK real estate crowdfunding sites:
http://www.housewalrus.co.uk
http://tiderock.co.uk
https://www.fundquarry.com

Of the above, only tiderock has a nice clean looking landing page. Information is clear and well laid out.

Hi all, just uploaded a new file in the brief. Contains some comments and a website reference. I thought it may help to explain how we could convey international aspect as well as how we could convey images in a more modern way. This is an option you can consider, but its entirely up to you how how answer the brief. Thanks!

Reason: As requested by some designers needing more time to complete their work. Continue to share your work in progress and receive timely feedback before the deadline.

We would like to let you know that we have just shortlisted the best designs. Together with that, we have also passed some detailed feedback to all designers who weren't shortlisted. If we didn't contact you, please let us know. If you haven't submitted a design or are working on revisions, please note these will no longer be taken into account now. We hope you understand that we need to close the project today. Thank you all once again for your great work and design concepts. Here's hoping we meet again on a future design brief. Cheers, pennyduke team.

Target Market(s)

At the moment, only rich are able to buy real estate. With this service, anyone can become a landlord. Target buyers:

Young professionals, looking to diversify from stock market and lower risk
People nearing retirement, looking for stable rental incomes
Retirees - looking to supplement pensions with possibility of capital gains
Parents - looking for a way to save long term for their children (instead of low interest paying bank accounts)

Industry/Entity Type

Communication

Font styles to use
Sans Serif
Other font styles liked:
• harabara

Colors
add136
f5f9eb
959595
000000

Requirements
Must have
• Overall, the site must convey "whoever you are, you too can become a landlord", and that you don't need to be wealthy to invest in real estate. See

Communication should put the investor (or the baron) at the centre. The investor can be any of those described in the target market.

Show the aspirational side of property ownership.

In addition to the investor/baron character, the second main theme is international. No other real estate crowdfunding website highlights this.
Nice to have
• Banner could show different consumer types, to illustrate that the service can appeal to many different profiles. Refer to attached file "home page reference - plainasbread.com" as an example of how this could be done.

Aim to show the international side of the service. Properties around the world, investors around the world.

```html
<!DOCTYPE html>
<html lang="en">
<head>
<meta charset="utf-8">
<title>pennyduke – Social real estate investment</title>
<link href="https://fonts.googleapis.com/css2?family=Nunito:wght@700;800&family=Open+Sans:wght@400;600;700&display=swap" rel="stylesheet">
<style>
:root{
  --green:#8dc63f;
  --green-dark:#7ab030;
  --green-pale:#f5f9eb;
  --ink:#3a3a3a;
  --text:#666666;
  --muted:#959595;
  --line:#dddddd;
  --panel:#f4f4f4;
  --dark:#4a4a4a;
  --darker:#2f2f2f;
  --white:#ffffff;
}
*{box-sizing:border-box;margin:0;padding:0}
html,body{width:1200px;height:3000px;overflow:hidden;background:var(--white)}
body{font-family:"Open Sans",Arial,sans-serif;color:var(--text);position:relative}
.display{font-family:"Nunito","Open Sans",sans-serif;font-weight:800}
.accent{color:var(--green);font-weight:600}

/* header */
.site-header{position:absolute;left:0;top:0;width:1200px;height:100px;background:var(--white)}
.brand{position:absolute;left:152px;top:24px;display:flex;align-items:center;gap:12px}
.brand-mark{width:40px;height:40px;border-radius:50%;background:var(--green)}
.brand-name{font-family:"Open Sans",sans-serif;font-weight:700;font-size:28px;color:var(--green)}
.follow{position:absolute;left:618px;top:24px;display:flex;align-items:center;gap:8px;font-size:14px;color:var(--ink)}
.social-box{width:34px;height:28px;background:var(--green)}
.social-box.alt{background:transparent;border:2px solid #777}
.search{position:absolute;left:810px;top:24px;width:246px;height:28px;display:flex}
.search-field{flex:1;background:#f0f0f0;font-size:11px;color:#aaa;padding:6px 10px}
.search-btn{width:36px;background:#555;display:flex;align-items:center;justify-content:center}
.main-nav{position:absolute;right:144px;top:72px;display:flex;gap:28px;font-size:11.5px;font-weight:600;color:#555;text-transform:uppercase}
.main-nav .current{color:var(--ink);font-weight:700;border-bottom:2px solid var(--ink);padding-bottom:4px}

/* hero */
.hero{position:absolute;left:0;top:100px;width:1200px;height:386px;background:linear-gradient(180deg,#7d7f80 0%,#a9abac 45%,#cfd0d0 100%);overflow:hidden}
.hero-photo{position:absolute;inset:0;background:linear-gradient(90deg,rgba(60,60,60,.35) 0%,rgba(255,255,255,0) 40%,rgba(0,0,0,.05) 100%)}
.hero-caption{position:absolute;left:146px;top:150px;width:504px}
.hero-title{background:var(--green);color:var(--white);font-family:"Nunito",sans-serif;font-weight:800;font-size:25px;padding:8px 18px 6px}
.hero-sub{background:rgba(141,198,63,.85);color:var(--white);font-size:14px;padding:4px 18px 10px}
.hero-arrow{position:absolute;top:168px;width:44px;height:44px;border-radius:50%;background:#2d2d2d;display:flex;align-items:center;justify-content:center}
.hero-arrow.prev{left:94px}.hero-arrow.next{left:1062px}
.hero-dots{position:absolute;left:130px;top:366px;display:flex;gap:4px}
.hero-dots span{width:9px;height:9px;border-radius:50%;background:#666}
.hero-dots span.on{background:var(--green)}

/* intro */
.intro{position:absolute;left:0;top:486px;width:1200px;height:304px;text-align:center}
.section-title{color:var(--green);font-size:29px;margin-top:50px}
.rule{width:340px;height:1px;background:var(--line);margin:14px auto 20px}
.intro p{font-size:13.5px;line-height:24px;margin-bottom:14px}

/* choose */
.choose{position:absolute;left:0;top:790px;width:1200px;height:304px;background:var(--panel)}
.choice{position:absolute;top:52px;width:368px}
.choice.left{left:202px}.choice.right{left:630px}
.choice-box{height:144px;background:var(--white);border:1px solid var(--line);display:flex;padding:24px 18px;gap:20px}
.choice-icon{width:80px;height:80px;border-radius:50%;background:#444;flex:none}
.choice-title{color:var(--green);font-family:"Nunito",sans-serif;font-weight:800;font-size:21px;margin-bottom:6px}
.choice-text{font-size:13px;line-height:23px}
.choice-btn{margin-top:12px;height:44px;background:var(--green);border-bottom:3px solid var(--green-dark);color:var(--white);font-family:"Nunito",sans-serif;font-weight:800;font-size:21px;text-align:center;line-height:42px}

/* projects */
.projects{position:absolute;left:0;top:1094px;width:1200px;height:620px;text-align:center}
.projects .section-title{font-size:21px;margin-top:34px}
.projects .lead{font-size:13px;line-height:24px;width:520px;margin:14px auto 0}
.project-card{position:absolute;top:144px;width:292px;height:416px;border:1px solid var(--line);background:var(--white);text-align:left}
.project-card:nth-of-type(1){left:144px;box-shadow:0 2px 6px rgba(0,0,0,.18)}
.project-card:nth-of-type(2){left:455px}
.project-card:nth-of-type(3){left:764px}
.project-photo{height:206px;position:relative}
.photo-a{background:linear-gradient(180deg,#3f7fd0 0%,#8db8e6 45%,#9b5a44 60%,#b9b6ae 85%)}
.photo-b{background:linear-gradient(180deg,#4a88d6 0%,#a8c7ea 45%,#c9b69a 60%,#c7c3b8 85%)}
.photo-c{background:linear-gradient(180deg,#1f70d2 0%,#7eb3ea 40%,#d9cfb9 60%,#4d7a3d 90%)}
.tag{position:absolute;left:0;color:var(--white);font-size:10px;font-weight:700;padding:3px 10px}
.tag.price{top:0;background:var(--green)}
.tag.new{top:22px;background:#6a6a54;font-weight:600}
.project-name{color:var(--green);font-size:15px;font-weight:600;padding:14px 18px 6px}
.project-text{font-size:11.5px;line-height:18px;padding:0 18px;color:#555}
.funded{font-size:12px;font-weight:700;color:#444;padding:22px 12px 4px}
.bar{margin:0 12px;height:20px;border:1px solid #bbb;border-radius:3px;position:relative;background:var(--white)}
.bar-fill{position:absolute;left:0;top:0;bottom:0;background:var(--green);border-radius:2px 0 0 2px}
.bar-label{position:absolute;left:0;right:0;text-align:center;font-size:11px;line-height:18px;color:#333}
.project-link{text-align:center;font-size:13px;font-weight:600;color:#777;padding-top:10px}
.project-card:nth-of-type(1) .project-link{color:var(--green)}

/* community */
.community{position:absolute;left:0;top:1714px;width:1200px;height:426px;background:linear-gradient(180deg,#3b3b3b 0%,#555 45%,#3a3a3a 100%);text-align:center}
.community-scene{position:absolute;inset:0;background:linear-gradient(180deg,rgba(0,0,0,0) 50%,rgba(0,0,0,.25) 100%)}
.community .section-title{font-size:21px;margin-top:56px;position:relative}
.community .lead{position:relative;font-size:14px;line-height:24px;color:#9a9a9a;width:640px;margin:10px auto 0}
.stat{position:absolute;top:190px;width:280px}
.stat.s1{left:120px}.stat.s2{left:460px}.stat.s3{left:770px}
.stat-map{position:absolute;left:10px;top:0;width:260px;height:110px;background:rgba(255,255,255,.07);border-radius:40px}
.stat-figure{position:relative;color:var(--green);font-size:19px;font-weight:700;line-height:24px;padding-top:44px}
.stat-text{position:relative;color:#ddd;font-size:14.5px;line-height:24px;margin-top:36px}

/* featured in */
.press{position:absolute;left:0;top:2140px;width:1200px;height:255px}
.press-frame{position:absolute;left:144px;top:58px;width:912px;height:192px;border:1px solid var(--line)}
.press-label{position:absolute;left:522px;top:40px;width:174px;height:36px;background:var(--green);color:var(--white);font-size:15px;font-weight:600;text-align:center;line-height:36px}
.press-badge{position:absolute;height:26px;background:#7a7a7a;border-radius:3px;opacity:.8}

/* skyline + footer */
.skyline{position:absolute;left:0;top:2395px;width:1200px;height:146px;background:linear-gradient(180deg,#ffffff 0%,#d4d4d4 45%,#a5a5a5 100%)}
.footer-bar{position:absolute;left:0;top:2541px;width:1200px;height:68px;background:var(--dark);display:flex;align-items:center;padding:0 144px;color:var(--green);font-size:16px;font-weight:600}
.footer-bar .social-box{width:40px;height:32px;background:transparent;border:2px solid var(--green);margin-left:10px}
.copyright{margin-left:auto;font-size:13px}
.legal{position:absolute;left:0;top:2609px;width:1200px;height:391px;background:var(--panel);padding:26px 144px 0}
.legal p{font-size:12.5px;line-height:22px;color:#666;margin-bottom:20px}
.legal .intro-line{width:580px}
.group-name{position:absolute;left:842px;top:26px;font-size:38px;font-weight:400;color:#444;line-height:1}
.group-name small{display:block;font-size:30px;color:#777;margin-left:78px}
</style>
</head>
<body>

<header class="site-header">
  <div class="brand"><span class="brand-mark"></span><span class="brand-name">pennyduke</span></div>
  <div class="follow">Follow us on <span class="social-box" aria-label="Social profile one"></span><span class="social-box alt" aria-label="Social profile two"></span></div>
  <div class="search">
    <div class="search-field">Search...</div>
    <div class="search-btn"><svg width="14" height="14" viewBox="0 0 14 14"><circle cx="6" cy="6" r="4.5" fill="none" stroke="#fff" stroke-width="2"/><line x1="9.2" y1="9.2" x2="13" y2="13" stroke="#fff" stroke-width="2"/></svg></div>
  </div>
  <nav class="main-nav">
    <span class="current">Home</span><span>Sign in</span><span>How it works</span><span>Discover a project</span><span>The baron blog</span><span>Find out more</span>
  </nav>
</header>

<section class="hero">
  <div class="hero-photo" role="img" aria-label="City skyline in grey tones with stacks of coins topped by small green houses"></div>
  <div class="hero-caption">
    <div class="hero-title">One property at a time</div>
    <div class="hero-sub">Invest from 1% in a property. Diversify across cities and properties.</div>
  </div>
  <div class="hero-arrow prev"><svg width="12" height="14" viewBox="0 0 12 14"><path d="M8 2 3 7l5 5" fill="none" stroke="#fff" stroke-width="2.4"/></svg></div>
  <div class="hero-arrow next"><svg width="12" height="14" viewBox="0 0 12 14"><path d="M4 2l5 5-5 5" fill="none" stroke="#fff" stroke-width="2.4"/></svg></div>
  <div class="hero-dots"><span class="on"></span><span></span><span></span><span></span></div>
</section>

<section class="intro">
  <h1 class="section-title display">Social real estate investment</h1>
  <div class="rule"></div>
  <p>By harnessing the power of crowds, it's possible to become a landlord in locations around the world. Forget the burden of<br>financing <span class="accent">100%</span> of the purchase.</p>
  <p>Leave the day to day management of your property portfolio to us.</p>
  <p>Start with <span class="accent">1%</span> in a project and plan your steps to becoming a true baron</p>
</section>

<section class="choose">
  <div class="choice left">
    <div class="choice-box">
      <div class="choice-icon"><svg width="80" height="80" viewBox="0 0 80 80"><rect x="26" y="30" width="10" height="28" fill="#8dc63f"/><rect x="38" y="22" width="12" height="36" fill="#8dc63f"/><rect x="52" y="36" width="8" height="22" fill="#8dc63f"/></svg></div>
      <div><div class="choice-title">Find properties</div><div class="choice-text">Sign up to browse the portfolio.<br>Your journey to becoming a real<br>estate baron starts here.</div></div>
    </div>
    <div class="choice-btn">Become a member</div>
  </div>
  <div class="choice right">
    <div class="choice-box">
      <div class="choice-icon" role="img" aria-label="Icon of a group of buyers"></div>
      <div><div class="choice-title">Find Buyers</div><div class="choice-text">Submit a property or development<br>and raise funds from our real estate<br>barons.</div></div>
    </div>
    <div class="choice-btn">Submit a property</div>
  </div>
</section>

<section class="projects">
  <h2 class="section-title display">Featured Projects</h2>
  <p class="lead">Brief details of new and popular projects. To view full listings, you will be required to sign up and <span class="accent">become a member</span>.</p>

  <article class="project-card">
    <div class="project-photo photo-a" role="img" aria-label="Red brick family house with a double garage"><span class="tag price">From GBP 3,600</span><span class="tag new">New Launch</span></div>
    <div class="project-name">21 Harrow Quay LONDON E1</div>
    <p class="project-text">Lorem Ipsum is simply dummy text of the printing and typesetting industry. Lorem Ipsum has been the industry's..</p>
    <div class="funded">Funded</div>
    <div class="bar"><div class="bar-fill" style="width:50%"></div><div class="bar-label">50%</div></div>
    <div class="project-link">See Project Details</div>
  </article>
  <article class="project-card">
    <div class="project-photo photo-b" role="img" aria-label="Cream and brick suburban house with a garage"><span class="tag price">From GBP 3,600</span><span class="tag new">New Launch</span></div>
    <div class="project-name">21 Harrow Quay LONDON E1</div>
    <p class="project-text">Lorem Ipsum is simply dummy text of the printing and typesetting industry. Lorem Ipsum has been the industry's..</p>
    <div class="funded">Funded</div>
    <div class="bar"><div class="bar-fill" style="width:75%"></div><div class="bar-label">75%</div></div>
    <div class="project-link">See Project Details</div>
  </article>
  <article class="project-card">
    <div class="project-photo photo-c" role="img" aria-label="White villa with a tiled tower among palm trees"><span class="tag price">From GBP 3,600</span><span class="tag new">New Launch</span></div>
    <div class="project-name">21 Harrow Quay LONDON E1</div>
    <p class="project-text">Lorem Ipsum is simply dummy text of the printing and typesetting industry. Lorem Ipsum has been the industry's..</p>
    <div class="funded">Funded</div>
    <div class="bar"><div class="bar-fill" style="width:40%"></div><div class="bar-label">40%</div></div>
    <div class="project-link">See Project Details</div>
  </article>
</section>

<section class="community">
  <div class="community-scene" role="img" aria-label="Dark aerial view of a city at dusk"></div>
  <h2 class="section-title display">Be Part of a Growing International Community</h2>
  <p class="lead">Gain access to new projects in world class cities and join our growing community of international landlords.</p>
  <div class="stat s1"><div class="stat-map" role="img" aria-label="Faint world map with location pins"></div><div class="stat-figure">3,200 barons<br>in 6 countries</div><div class="stat-text">A community of international<br>property barons.</div></div>
  <div class="stat s2"><div class="stat-map" role="img" aria-label="Faint group of people"></div><div class="stat-figure">USD$ 16.2 million</div><div class="stat-text">Collective buying power of<br>the pennyduke community</div></div>
  <div class="stat s3"><div class="stat-map" role="img" aria-label="Faint world map with location pins"></div><div class="stat-figure">64 proposals in 6<br>countries</div><div class="stat-text">Attractive real estate from<br>around the world</div></div>
</section>

<section class="press">
  <div class="press-frame">
    <div class="press-badge" style="left:-54px;top:0;width:0"></div>
  </div>
  <div class="press-badge" style="left:180px;top:2140px"></div>
  <div class="press-label">Featured In</div>
  <div class="press-badge" style="left:180px;top:128px;width:110px"></div>
  <div class="press-badge" style="left:322px;top:128px;width:160px"></div>
  <div class="press-badge" style="left:514px;top:124px;width:130px;height:30px"></div>
  <div class="press-badge" style="left:682px;top:128px;width:340px"></div>
  <div class="press-badge" style="left:306px;top:194px;width:60px;height:30px"></div>
  <div class="press-badge" style="left:396px;top:198px;width:130px;height:22px"></div>
  <div class="press-badge" style="left:558px;top:190px;width:40px;height:38px"></div>
  <div class="press-badge" style="left:640px;top:190px;width:70px;height:38px"></div>
  <div class="press-badge" style="left:738px;top:194px;width:140px;height:30px"></div>
</section>

<div class="skyline" role="img" aria-label="Grey skyline silhouette of world landmark cities"></div>

<footer>
  <div class="footer-bar">Follow us on <span class="social-box" aria-label="Social profile one"></span><span class="social-box" aria-label="Social profile two"></span><span class="copyright">© pennyduke 2014</span></div>
  <div class="legal">
    <div class="group-name">sproutledger<small>group</small></div>
    <p class="intro-line"><span class="accent">Penny Duke</span> is part of the Sprout Ledger Group. The Sprout Ledger Group is a worldwide pioneer and leader in the crowd investing, peer to peer and online investment market.</p>
    <p>By accessing this site and any pages thereof, you agree to be bound by the terms and conditions. This website is only suitable, intended and available for professional or sophisticated, or similar investors in other jurisdictions, or those who are members of pennyduke community and familiar with, and willing to, accept the risks associated with private participation. Pennyduke does not endorse any of the projects that appear on this website, nor does it make any recommendations regarding the appropriateness of particular opportunities for any participant. Each potential participant must review and evaluate the projects in his or her own discretion and determine the suitability of participating.</p>
    <p>This website (the "Site") is in every respect unaffiliated with any site to which it links or to any company or entity (and connected projects, investment opportunity or similar) featured on this Site, and is not meant as an endorsement of any of those companies or entities ("third parties"). Furthermore and for the avoidance of doubt, Pennyduke Limited is in no way affiliated with any third parties featured or referenced on this Site. There is no commercial relationship between Pennyduke Limited and such third parties, nor an agency arrangement or similar. If you believe your Content (including third party content) as each such term is defined in our Terms of Service has been reproduced on the Site without permission, please refer to our Terms of Service for information on how to request its removal from the Site.</p>
  </div>
</footer>

</body>
</html>
```